Web Design Project for Communications Agency

The design I need (PSD file) is for an agency offering specialised PR and communications services for customers in the healthcare sector.

OBJECTIVES OF THE WEBSITE:
1. To promote the agency's communication services
2. To position Solène Brivard as an industry leader, an expert in healthcare PR and communications by highlighting blogposts and social media.

WHAT I NEED:
1st, I need the design for the Home Page ONLY.
Once approved, I will need the other pages designed as well. (Here is prototype that we've already developed for the Website that will guide you in the design:
http://qorvelle.net/solenebrivard/)

VISUAL INSPIRATION
We want to give this Website a "Flat Design" look. Here are some websites for inspiration :
- http://tavrolinkworks.com/#!/process
- http://www.brindlemoss.co/
- http://quellaroft.com/

Also, reuse images found on the company's current Website :
http://www.solenebrivard.com/fr/index.html

HOMEPAGE MAIN ELEMENTS:
1. Main menu : 6 sections
Accueil | Agence | Services | Approche | Publications | Contact

2. Main Call To Action (big dark rectangle in prototype):
Can be slider or just an information bloc.

3. Publications récentes :
The 4 latest blog posts must be features on the homepage (will be linked with the "Publications" section)

4. Dynamic Footer :
Contains a Chirpline feed and a Subscribe to our Newsletter feature (revecez nos publications)

OTHER PAGES (to design once Homepage is approved)
- Agence (about us)
- Services (our team)
- Approche (our approach)
- Publications (blog articles)
- Contact (Contact us)

Industry/Entity Type

Communications

Requirements
Must have
• Please refer to prototype :
http://qorvelle.net/solenebrivard/
Must have ALL features present in prototype.

Also, must reuse this picture in the design : http://solenebrivard.com/static/images/home-big-box.jpg

Finally, you will find attached the company logo.

```html
<!DOCTYPE html>
<html lang="fr">
<head>
<meta charset="utf-8">
<title>Solène Brivard – Gestion d'enjeux</title>
<link href="https://fonts.googleapis.com/css2?family=Oswald:wght@300;400&display=swap" rel="stylesheet">
<style>
:root{
  --red:#c41e2b;
  --red-dark:#a8161f;
  --red-soft:#d6404a;
  --ink:#4a4a4a;
  --text:#6b6b6b;
  --hero:#e6e6e6;
  --nav:#efefef;
  --line:#d2d2d2;
  --footer:#2e2e2e;
  --sky:#2ba8e2;
  --white:#fff;
}
*{box-sizing:border-box;margin:0;padding:0}
html,body{width:758px;height:1200px;overflow:hidden;background:var(--white)}
body{position:relative;font-family:Arial,Helvetica,sans-serif;color:var(--text)}
.abs{position:absolute}
.oswald{font-family:'Oswald',sans-serif}

/* header */
.brand{left:74px;top:8px}
.brand-name{font-family:'Oswald',sans-serif;font-weight:400;color:var(--red);font-size:21px;line-height:20px;width:80px;text-transform:lowercase;letter-spacing:-.3px}
.brand-tag{font-family:'Oswald',sans-serif;font-size:6px;line-height:7px;color:#555;margin-top:3px;letter-spacing:.3px}
.brand-tag span{display:block;width:14px;height:1px;background:var(--red);margin-top:2px}
.lang{left:534px;top:10px;width:64px;height:19px;border:1px solid #ddd;font-size:7px;color:#333;padding:5px 0 0 8px}
.lang::before{content:"";display:inline-block;width:9px;height:6px;background:#4a5ea8;margin-right:5px;vertical-align:-1px}
.lang::after{content:"";position:absolute;right:6px;top:6px;border:4px solid transparent;border-top:5px solid var(--red)}
.social{top:9px;width:20px;height:20px;border-radius:5px}
.social.s1{left:610px;background:#3a63b4}
.social.s2{left:635px;background:#35a9e1}
.social.s3{left:660px;background:#d7292a}

.nav{left:0;top:60px;width:758px;height:24px;background:linear-gradient(#f6f6f6,#e9e9e9);border-top:1px solid #e0e0e0;border-bottom:1px solid var(--line)}
.nav a{position:absolute;top:5px;transform:translateX(-50%);font-family:'Oswald',sans-serif;font-size:9px;color:#555;text-decoration:none;text-transform:uppercase}
.nav a.active{color:var(--red)}

/* hero */
.hero{left:0;top:84px;width:758px;height:279px;background:linear-gradient(90deg,#e2e2e2,#ececec 60%,#e4e4e4);border-bottom:2px solid #d8d8d8}
.hero-title{left:76px;top:61px;width:352px;font-family:'Oswald',sans-serif;font-weight:400;font-size:16px;line-height:19px;color:var(--red);text-transform:uppercase;letter-spacing:-.4px}
.hero-text{left:76px;top:116px;width:348px;font-family:'Oswald',sans-serif;font-weight:300;font-size:9px;line-height:12.8px;color:#444;text-transform:uppercase;text-align:justify}
.btn{background:var(--red);color:var(--white);font-family:'Oswald',sans-serif;text-transform:uppercase;text-align:center;border-radius:1px}
.hero-btn{left:76px;top:188px;width:55px;height:22px;font-size:9px;line-height:22px}
.dots{left:75px;top:249px;display:flex;gap:3px}
.dots i{width:6px;height:6px;border-radius:50%;background:#aaa}
.dots i.on{background:#444}
.hero-visual{left:432px;top:20px;width:248px;height:248px;background:radial-gradient(circle at 50% 45%,#fafafa,#dcdcdc 70%,transparent 72%)}

/* publications */
.section-title{left:75px;top:376px;font-family:'Oswald',sans-serif;font-size:13px;color:var(--red);text-transform:uppercase}
.post{left:75px;width:608px;height:140px}
.post-media{position:absolute;left:0;top:0;width:297px;height:139px}
.post-body{position:absolute;left:310px;top:0;width:298px}
.post-title{font-family:'Oswald',sans-serif;font-size:9.5px;color:var(--red);text-transform:uppercase;margin-top:1px}
.post-date{font-family:'Oswald',sans-serif;font-weight:300;font-size:7.5px;color:#444;margin-top:5px}
.post-text{font-size:7px;line-height:12px;color:#666;text-align:justify;margin-top:4px}
.post-link{font-size:7.2px;font-weight:bold;color:var(--red);margin-top:11px}
.m1{background:linear-gradient(90deg,#4e8a2a,#b9d7a9 50%,#9ec37c)}
.m2{background:linear-gradient(90deg,#c9d8e4,#a9bccc 50%,#1e1e1e 70%,#2a2a2a)}
.m3{background:linear-gradient(135deg,#d9d2c4,#4a6fa8 45%,#8a5a2c 80%,#d8c9b4)}
.m4{background:linear-gradient(90deg,#6d88ab,#28354e 40%,#bcd2e8 55%,#2b3850)}

/* footer */
.footer{left:0;top:1027px;width:758px;height:149px;background:var(--footer)}
.feed-name{left:75px;top:1034px;font-family:'Oswald',sans-serif;font-size:22px;color:var(--sky)}
.feed-follow{left:284px;top:1047px;font-size:7.5px;color:var(--sky)}
.tweet{left:76px;width:297px;font-size:7.3px;line-height:12px;color:#ddd}
.tweet b{font-weight:normal;color:var(--red-soft)}
.sub-title{left:429px;top:1041px;font-family:'Oswald',sans-serif;font-weight:300;font-size:16px;color:var(--red-soft);text-transform:uppercase}
.field{left:430px;width:251px;height:28px;background:var(--white);font-size:7.3px;color:#555;padding:10px 0 0 5px}
.sub-btn{left:620px;top:1140px;width:61px;height:28px;font-size:8px;line-height:28px;letter-spacing:-.2px}
.bar{left:0;top:1176px;width:758px;height:24px;background:var(--red-dark);color:var(--white);font-size:7.3px}
.bar .copy{position:absolute;left:76px;top:8px}
.bar .links{position:absolute;right:76px;top:8px}
</style>
</head>
<body>

<header>
  <div class="abs brand">
    <div class="brand-name">Solène Brivard</div>
    <div class="brand-tag">GESTION D'ENJEUX<br>AFFAIRES PUBLIQUES<span></span></div>
  </div>
  <div class="abs lang">English</div>
  <div class="abs social s1" role="img" aria-label="Réseau social"></div>
  <div class="abs social s2" role="img" aria-label="Réseau social"></div>
  <div class="abs social s3" role="img" aria-label="Chaîne vidéo"></div>
</header>

<nav class="abs nav">
  <a class="active" style="left:258px">Accueil</a>
  <a style="left:330px">Agence</a>
  <a style="left:403px">Services</a>
  <a style="left:482px">Approche</a>
  <a style="left:569px">Publications</a>
  <a style="left:653px">Contact</a>
</nav>

<section class="abs hero">
  <h1 class="abs hero-title">Cabinet-conseil en communications et affaires publiques spécialisé dans le secteur de la santé.</h1>
  <p class="abs hero-text">Nous sommes un cabinet-conseil en communications et affaires publiques spécialisé dans le secteur de la santé. Nous accompagnons les associations, les ordres professionnels, les entreprises privées, les centres de recherche dans leur stratégie de positionnement afin qu'ils saisissent les opportunités d'un marché porteur, mais scruté par l'opinion publique et les leaders d'opinion.</p>
  <div class="abs btn hero-btn">Read more</div>
  <div class="abs dots"><i></i><i></i><i class="on"></i><i></i><i></i></div>
  <div class="abs hero-visual" role="img" aria-label="Cube blanc en trois dimensions avec une croix rouge sur sa face supérieure"></div>
</section>

<h2 class="abs section-title">Publication récentes</h2>

<article class="abs post" style="top:402px">
  <div class="post-media m1" role="img" aria-label="Globe de verre posé dans l'herbe verte"></div>
  <div class="post-body">
    <h3 class="post-title">Titre de la publication</h3>
    <div class="post-date">23 JUILLET 2013</div>
    <p class="post-text">Lorem ipsum dolor sit amet, consectetur adipisicing elit, sed do eiusmod tempor incididunt ut labore et dolore magna aliqua. Ut enim ad minim veniam, quis nostrud exercitation ullamco laboris nisi ut aliquip ex ea commodo consequat. Duis aute irure dolor in reprehenderit in voluptate velit esse cillum dolore eu fugiat nulla pariatur. Excepteur sint occaecat cupidatat non proident, Velit esse cillum dolore eu fugiat nulla pariatur. Excepteur sint occaecat cupidatat non proident, sunt in culpa qui officia deserunt mollit anim id est laborum. Velit esse cillum dolore eu fugiat nulla pariatur.</p>
    <div class="post-link">Article complet</div>
  </div>
</article>

<article class="abs post" style="top:560px">
  <div class="post-media m2" role="img" aria-label="Homme d'affaires en costume, bras croisés, dans un bureau lumineux"></div>
  <div class="post-body">
    <h3 class="post-title">Titre de la publication</h3>
    <div class="post-date">23 JUILLET 2013</div>
    <p class="post-text">Lorem ipsum dolor sit amet, consectetur adipisicing elit, sed do eiusmod tempor incididunt ut labore et dolore magna aliqua. Ut enim ad minim veniam, quis nostrud exercitation ullamco laboris nisi ut aliquip ex ea commodo consequat. Duis aute irure dolor in reprehenderit in voluptate velit esse cillum dolore eu fugiat nulla pariatur. Excepteur sint occaecat cupidatat non proident, Velit esse cillum dolore eu fugiat nulla pariatur. Excepteur sint occaecat cupidatat non proident, sunt in culpa qui officia deserunt mollit anim id est laborum. Velit esse cillum dolore eu fugiat nulla pariatur.</p>
    <div class="post-link">Article complet</div>
  </div>
</article>

<article class="abs post" style="top:718px">
  <div class="post-media m3" role="img" aria-label="Pelle plantée dans un tas de terre sur fond bleu"></div>
  <div class="post-body">
    <h3 class="post-title">Titre de la publication</h3>
    <div class="post-date">23 JUILLET 2013</div>
    <p class="post-text">Lorem ipsum dolor sit amet, consectetur adipisicing elit, sed do eiusmod tempor incididunt ut labore et dolore magna aliqua. Ut enim ad minim veniam, quis nostrud exercitation ullamco laboris nisi ut aliquip ex ea commodo consequat. Duis aute irure dolor in reprehenderit in voluptate velit esse cillum dolore eu fugiat nulla pariatur. Excepteur sint occaecat cupidatat non proident, Velit esse cillum dolore eu fugiat nulla pariatur. Excepteur sint occaecat cupidatat non proident, sunt in culpa qui officia deserunt mollit anim id est laborum. Velit esse cillum dolore eu fugiat nulla pariatur.</p>
    <div class="post-link">Article complet</div>
  </div>
</article>

<article class="abs post" style="top:876px">
  <div class="post-media m4" role="img" aria-label="Mains tenant un petit globe terrestre devant un costume sombre"></div>
  <div class="post-body">
    <h3 class="post-title">Titre de la publication</h3>
    <div class="post-date">23 JUILLET 2013</div>
    <p class="post-text">Lorem ipsum dolor sit amet, consectetur adipisicing elit, sed do eiusmod tempor incididunt ut labore et dolore magna aliqua. Ut enim ad minim veniam, quis nostrud exercitation ullamco laboris nisi ut aliquip ex ea commodo consequat. Duis aute irure dolor in reprehenderit in voluptate velit esse cillum dolore eu fugiat nulla pariatur. Excepteur sint occaecat cupidatat non proident, Velit esse cillum dolore eu fugiat nulla pariatur. Excepteur sint occaecat cupidatat non proident, sunt in culpa qui officia deserunt mollit anim id est laborum. Velit esse cillum dolore eu fugiat nulla pariatur.</p>
    <div class="post-link">Article complet</div>
  </div>
</article>

<footer>
  <div class="abs footer"></div>
  <div class="abs feed-name">Chirpline</div>
  <div class="abs feed-follow">Follow @SoleneBrivard</div>
  <p class="abs tweet" style="top:1077px">Velit esse cillum dolore eu fugiat nulla pariatur. Excepteur sint occaecat cupidatat non proident. <b>@SoleneBrivard #EnjeuSanté</b></p>
  <p class="abs tweet" style="top:1109px">Velit esse cillum dolore eu fugiat nulla pariatur. Excepteur sint occaecat cupidatat non proident. <b>@SoleneBrivard #EnjeuSanté</b></p>
  <p class="abs tweet" style="top:1141px">Velit esse cillum dolore eu fugiat nulla pariatur. Excepteur sint occaecat cupidatat non proident. <b>@SoleneBrivard #EnjeuSanté</b></p>

  <h2 class="abs sub-title">Recevez nos publications</h2>
  <div class="abs field" style="top:1072px">Votre nom</div>
  <div class="abs field" style="top:1106px">Votre courriel</div>
  <div class="abs btn sub-btn">ABONNEZ-VOUS</div>

  <div class="abs bar">
    <span class="copy">(c) Solène Brivard. Tous droits réservés.</span>
    <span class="links">Agence | Services | Approche | Publications | Contact | Accueil|</span>
  </div>
</footer>

</body>
</html>
```